Business Cards for a law firm

Business cards for our law firm. Use our silhoette logo and OAK PARTNERS - check our website (www.oakpartners.example)

Contact Information for Business Card

our silhouette logo, OAK PARTNERS, 800-555-0147, Dorian Pemberton, dorian@oakpartners.example

Requirements
Must have
• our silhouette logo, OAK PARTNERS, 800-555-0147, Dorian Pemberton, dorian@oakpartners.example

```html
<!DOCTYPE html>
<html lang="en">
<head>
<meta charset="utf-8">
<title>Oak Partners – Business Cards</title>
<link href="https://fonts.googleapis.com/css2?family=Open+Sans:wght@400;600;700&display=swap" rel="stylesheet">
<style>
  :root {
    --navy: #1f2e63;
    --paper: #f4f4f3;
    --backdrop: #d2d2d2;
    --accent: #f0a51c;
    --muted: #707070;
  }
  * { margin: 0; padding: 0; box-sizing: border-box; }
  html, body { width: 1200px; height: 853px; overflow: hidden; }
  body {
    background: var(--backdrop);
    font-family: "Open Sans", Arial, sans-serif;
    display: flex;
    flex-direction: column;
    align-items: center;
    justify-content: center;
    gap: 48px;
  }
  .card {
    position: relative;
    width: 560px;
    height: 320px;
    background: var(--paper);
    border-radius: 22px;
    overflow: hidden;
    color: var(--navy);
  }
  .brand {
    display: flex;
    align-items: center;
    gap: 10px;
    font-weight: 700;
    letter-spacing: 0.06em;
    color: var(--navy);
    white-space: nowrap;
  }
  .brand-mark { width: 26px; height: 26px; background: var(--navy); flex: none; }
  /* back */
  .card-back { display: flex; align-items: center; justify-content: center; }
  .card-back .brand { font-size: 30px; }
  .card-back .brand-mark { width: 36px; height: 36px; }
  /* front */
  .card-front .brand { position: absolute; top: 26px; left: 30px; font-size: 24px; }
  .firm { position: absolute; top: 100px; left: 34px; width: 220px; }
  .firm-name { font-size: 19px; font-weight: 600; letter-spacing: 0.02em; line-height: 1; white-space: nowrap; }
  .firm-tagline { font-size: 8.5px; letter-spacing: 0.42em; margin-top: 5px; color: var(--navy); white-space: nowrap; }
  .rule { width: 22px; height: 2px; background: var(--accent); margin: 11px 0 9px; }
  .person-name { font-size: 18px; font-weight: 600; line-height: 1.1; white-space: nowrap; }
  .person-title { font-size: 10px; color: var(--muted); letter-spacing: 0.05em; margin-top: 2px; }
  .contacts { list-style: none; margin-top: 12px; font-size: 10.5px; color: var(--muted); }
  .contacts li { display: flex; align-items: center; gap: 7px; margin-bottom: 5px; white-space: nowrap; }
  .contacts svg { width: 11px; height: 11px; fill: var(--accent); flex: none; }
  .illustration { position: absolute; right: 0; bottom: 0; width: 300px; height: 240px; }
</style>
</head>
<body>
  <section class="card card-back">
    <div class="brand"><span class="brand-mark"></span>OAK PARTNERS</div>
  </section>

  <section class="card card-front">
    <div class="brand"><span class="brand-mark"></span>OAK PARTNERS</div>

    <div class="firm">
      <p class="firm-name">OAK PARTNERS</p>
      <p class="firm-tagline">INJURY ATTORNEYS</p>
      <div class="rule"></div>
      <p class="person-name">Dorian Pemberton</p>
      <p class="person-title">ATTORNEY</p>
      <ul class="contacts">
        <li>
          <svg viewBox="0 0 24 24" aria-hidden="true"><path d="M6.6 10.8a15.1 15.1 0 0 0 6.6 6.6l2.2-2.2a1 1 0 0 1 1-.25 11.4 11.4 0 0 0 3.6.57 1 1 0 0 1 1 1V20a1 1 0 0 1-1 1A17 17 0 0 1 3 4a1 1 0 0 1 1-1h3.5a1 1 0 0 1 1 1c0 1.25.2 2.45.57 3.57a1 1 0 0 1-.25 1z"/></svg>
          800-555-0147
        </li>
        <li>
          <svg viewBox="0 0 24 24" aria-hidden="true"><path d="M2 5h20v14H2zm2 2v.5l8 5 8-5V7l-8 5z"/></svg>
          dorian@oakpartners.example
        </li>
        <li>
          <svg viewBox="0 0 24 24" aria-hidden="true"><path d="M12 2a10 10 0 1 0 0 20 10 10 0 0 0 0-20zm0 2.2a7.8 7.8 0 1 1 0 15.6 7.8 7.8 0 0 1 0-15.6z"/></svg>
          www.oakpartners.example
        </li>
      </ul>
    </div>

    <svg class="illustration" viewBox="0 0 300 240" preserveAspectRatio="none"
         role="img" aria-label="Illustration of two standing figures as white silhouettes on a navy field">
      <path d="M0 240 L40 170 L70 60 L120 30 L170 0 L300 0 L300 240 Z" fill="var(--navy)"/>
    </svg>
  </section>
</body>
</html>
```